Volbrey Inc Business Card

Looking to get an updated business card for a Contract Machining company (www.volbreyinc.example) - looking for a clean design the portrays the technical nature of the business - colors can follow the website design and be in any combination that makes sense (red black, white, metallic or silver) - logos attached for use also. Would like space for: Name, title, business phone (555 214-3086), cell phone , website (www.volbreyinc.example) - possibly QR code could be integrated for website (designer choice), business address - 418 Harlow Bend, Ashgrove, WI 48199 (cards will be for 4 employees, I will either need to modify a template or I can provide individual information)
Target Market(s)
Aerospace, defense and medical device manufacturing companies that need machining
Industry/Entity Type
Machining for aerospace, defense, medical
Contact Information for Business Card
Name, Title, Business Phone, Cell Phone, email, business website and business address
Look and feel

```html
<!DOCTYPE html>
<html lang="en">
<head>
<meta charset="utf-8">
<title>Volbrey Inc Business Card</title>
<link href="https://fonts.googleapis.com/css2?family=Poppins:wght@400;600;700&display=swap" rel="stylesheet">
<style>
  :root {
    --brand-red: #b31e24;
    --deep-red: #7a1418;
    --ink: #1c1c1c;
    --paper: #ffffff;
    --backdrop: #ababab;
  }
  * { box-sizing: border-box; margin: 0; padding: 0; }
  html, body {
    width: 1093px; height: 1200px; overflow: hidden;
    background: var(--backdrop);
    font-family: "Poppins", sans-serif;
  }
  .canvas { position: relative; width: 1093px; height: 1200px; }
  .card {
    position: absolute; left: 264px; width: 580px; height: 357px;
  }
  .card--front { top: 226px; background: var(--paper); }
  .card--back { top: 620px; background: var(--brand-red); }

  .name-marker {
    position: absolute; left: 0; top: 43px; width: 18px; height: 32px;
    background: var(--brand-red);
  }
  .identity { position: absolute; left: 29px; top: 40px; }
  .identity__name {
    font-weight: 700; font-size: 20px; line-height: 22px;
    color: var(--brand-red); letter-spacing: 0.1px;
  }
  .identity__title {
    font-weight: 400; font-size: 16.5px; line-height: 20px; color: var(--ink);
  }

  .wordmark {
    position: absolute; right: 37px; top: 36px; text-align: center;
    color: var(--brand-red); font-weight: 600;
  }
  .wordmark__name { font-size: 50px; line-height: 54px; letter-spacing: 0.5px; }
  .wordmark__suffix { font-size: 20px; line-height: 22px; letter-spacing: 1px; }

  .contact-list {
    position: absolute; left: 29px; top: 250px; list-style: none;
  }
  .contact-list li {
    display: flex; align-items: center; height: 21px;
    font-size: 16.5px; color: var(--ink);
  }
  .contact-list svg { width: 15px; height: 15px; margin-right: 7px; flex: none; }
  .accent { color: var(--brand-red); }

  .address {
    position: absolute; right: 37px; top: 292px; text-align: right;
    font-size: 16.5px; line-height: 21px; color: var(--ink); font-style: normal;
  }

  .base-band {
    position: absolute; left: 0; bottom: 0; width: 100%; height: 11px;
    background: var(--brand-red);
  }
  .base-band svg { position: absolute; right: 5px; top: 0; }

  .back-wordmark {
    position: absolute; inset: 0; display: flex; align-items: center; justify-content: center;
    font-weight: 700; font-size: 80px; letter-spacing: 1px; color: var(--deep-red);
  }
</style>
</head>
<body>
<main class="canvas">
  <section class="card card--front" aria-label="Business card front">
    <div class="name-marker"></div>
    <div class="identity">
      <p class="identity__name">DANIEL MARSH</p>
      <p class="identity__title">Managing Director</p>
    </div>

    <div class="wordmark">
      <p class="wordmark__name">VOLBREY</p>
      <p class="wordmark__suffix">INC.</p>
    </div>

    <ul class="contact-list">
      <li>
        <svg viewBox="0 0 24 24" aria-hidden="true"><path fill="var(--brand-red)" d="M6.6 10.8a15.2 15.2 0 0 0 6.6 6.6l2.2-2.2a1 1 0 0 1 1-.25 11.4 11.4 0 0 0 3.6.57 1 1 0 0 1 1 1V20a1 1 0 0 1-1 1A17 17 0 0 1 3 4a1 1 0 0 1 1-1h3.5a1 1 0 0 1 1 1c0 1.25.2 2.45.57 3.57a1 1 0 0 1-.25 1z"/><path fill="none" stroke="var(--brand-red)" stroke-width="2" d="M14 3a7 7 0 0 1 7 7M14 7a3 3 0 0 1 3 3"/></svg>
        555 214-3086
      </li>
      <li>
        <svg viewBox="0 0 24 24" aria-hidden="true"><rect x="6" y="2" width="12" height="20" rx="2" fill="none" stroke="var(--brand-red)" stroke-width="2"/><circle cx="12" cy="18" r="1.3" fill="var(--brand-red)"/></svg>
        555 907-4412
      </li>
      <li>
        <svg viewBox="0 0 24 24" aria-hidden="true"><rect x="2" y="5" width="20" height="14" fill="var(--brand-red)"/><path d="M2 5l10 8 10-8" fill="none" stroke="#fff" stroke-width="1.6"/></svg>
        info@volbreyinc.example
      </li>
      <li>
        <svg viewBox="0 0 24 24" aria-hidden="true"><g fill="none" stroke="var(--brand-red)" stroke-width="1.8"><circle cx="12" cy="12" r="9.5"/><ellipse cx="12" cy="12" rx="4" ry="9.5"/><path d="M2.5 12h19M4 7h16M4 17h16"/></g></svg>
        <span>www.<span class="accent">volbreyinc</span>.example</span>
      </li>
    </ul>

    <address class="address">
      418 Harlow Bend<br>
      Ashgrove, WI 48199
    </address>

    <div class="base-band">
      <svg width="40" height="11" viewBox="0 0 40 11" aria-hidden="true">
        <g fill="#fff">
          <polygon points="3,0 6,0 3,11 0,11"/>
          <polygon points="13,0 16,0 13,11 10,11"/>
          <polygon points="23,0 26,0 23,11 20,11"/>
          <polygon points="33,0 36,0 33,11 30,11"/>
        </g>
      </svg>
    </div>
  </section>

  <section class="card card--back" aria-label="Business card back">
    <p class="back-wordmark">VOLBREY</p>
  </section>
</main>
</body>
</html>
```